U.S. Popcorn company needs business cards

We are a popcorn company that manufactures popcorn and sells it to grocery stores worldwide. Our theme is "Americana" and our logo is U.S. route 66 which is the most famous highway in the U.S.

We would like the design to be simple and to use both sides. On the back side we would like to see just the logo and website. The front would be normal details

Target Market(s)

Wholesalers, grocers and distributors

Industry/Entity Type

Manufacture

Contact Information for Business Card

Business name: Prairie Lantern Popcorn
Phone: +1 555 308 4726
Email: Dale@prairielanternpopcorn.com
website: www.prairielanternpopcorn.com
Tag Line: "Worth every handful"
Name: Dale Whitcombe
Title: Founder/President

Requirements
Must have
• Either this design should be fun or clean and simple. I will let you show me your thougths.
Nice to have
• Anything that ties in the real Hwy Route 66.
• Colors might need to be red, white and blue incorporated.
Should not have
• Not be too busy.

```html
<!DOCTYPE html>
<html lang="en">
<head>
<meta charset="utf-8">
<title>Prairie Lantern Popcorn – Business Cards</title>
<link href="https://fonts.googleapis.com/css2?family=Open+Sans:wght@400;600&display=swap" rel="stylesheet">
<style>
  :root {
    --navy: #233a8c;
    --navy-deep: #1a2c72;
    --navy-light: #2f4ba8;
    --red: #e0262f;
    --paper: #f7f7f7;
    --ink-blue: #22358a;
    --stage: #e9e7e2;
  }
  * { margin: 0; padding: 0; box-sizing: border-box; }
  html, body { width: 1200px; height: 780px; overflow: hidden; }
  body {
    background: var(--stage);
    font-family: "Open Sans", Arial, sans-serif;
    position: relative;
  }
  .card {
    position: absolute;
    top: 235px;
    width: 540px;
    height: 310px;
    overflow: hidden;
    box-shadow: 0 6px 18px rgba(0,0,0,0.18);
  }

  /* Front */
  .card-front { left: 50px; background: var(--paper); }
  .brand-mark {
    position: absolute;
    left: 30px; top: 100px;
    width: 210px;
    display: flex; align-items: center; gap: 12px;
  }
  .brand-dot {
    flex: 0 0 34px; height: 34px; border-radius: 50%;
    background: var(--red);
  }
  .brand-name {
    color: var(--ink-blue);
    font-weight: 600;
    font-size: 22px;
    line-height: 1.2;
  }
  .divider {
    position: absolute;
    left: 262px; top: 60px;
    width: 1px; height: 150px;
    background: linear-gradient(to bottom, rgba(224,38,47,0), var(--red) 30%, var(--red) 70%, rgba(224,38,47,0));
  }
  .contact {
    position: absolute;
    left: 290px; top: 44px;
    color: var(--ink-blue);
  }
  .person-name { font-size: 25px; font-weight: 400; line-height: 1.1; }
  .person-title { font-size: 15px; color: var(--red); margin-bottom: 16px; }
  .address { font-size: 13px; line-height: 1.4; margin-bottom: 10px; }
  .contact-line {
    display: flex; align-items: center; gap: 7px;
    font-size: 12.5px; line-height: 1.55;
  }
  .contact-icon {
    width: 15px; height: 15px; background: var(--red);
    display: inline-flex; align-items: center; justify-content: center;
    flex: 0 0 15px;
  }
  .band-rule {
    position: absolute; left: 0; right: 0; bottom: 44px;
    height: 3px; background: var(--red);
    border-bottom: 2px solid #fff;
  }
  .band {
    position: absolute; left: 0; right: 0; bottom: 0;
    height: 42px; background: var(--navy);
    display: flex; align-items: center; justify-content: flex-end;
    padding-right: 150px;
  }
  .tagline { color: #fff; font-size: 14px; letter-spacing: 0.3px; }

  /* Back */
  .card-back {
    left: 610px;
    background: radial-gradient(ellipse at 45% 45%, var(--navy-light), var(--navy) 55%, var(--navy-deep));
    display: flex; flex-direction: column; align-items: center; justify-content: center;
    color: #fff;
  }
  .back-name {
    font-size: 30px; font-weight: 600; letter-spacing: 1px;
    text-transform: uppercase;
  }
  .back-web { font-size: 15px; margin-top: 8px; letter-spacing: 0.3px; }
</style>
</head>
<body>

<section class="card card-front" aria-label="Business card front">
  <div class="brand-mark">
    <span class="brand-dot"></span>
    <span class="brand-name">Prairie Lantern Popcorn</span>
  </div>
  <div class="divider"></div>
  <div class="contact">
    <p class="person-name">Dale Whitcombe</p>
    <p class="person-title">Founder/President</p>
    <p class="address">Lantern Falls, KS<br>United States</p>
    <p class="contact-line">
      <span class="contact-icon">
        <svg width="10" height="10" viewBox="0 0 10 10"><path d="M2 1 L4 1 L4.6 3 L3.5 3.8 Q4.4 5.7 6.2 6.5 L7 5.4 L9 6 L9 8 Q8.5 9 7.5 9 Q1 8.5 1 2.5 Q1 1.5 2 1 Z" fill="#fff"/></svg>
      </span>+1 555 308 4726
    </p>
    <p class="contact-line">
      <span class="contact-icon">
        <svg width="10" height="8" viewBox="0 0 10 8"><rect x="0.5" y="0.5" width="9" height="7" fill="none" stroke="#fff"/><path d="M0.5 0.5 L5 4.5 L9.5 0.5" fill="none" stroke="#fff"/></svg>
      </span>Dale@prairielanternpopcorn.com
    </p>
    <p class="contact-line">
      <span class="contact-icon">
        <svg width="10" height="10" viewBox="0 0 10 10"><circle cx="5" cy="5" r="4.2" fill="none" stroke="#fff"/><ellipse cx="5" cy="5" rx="1.8" ry="4.2" fill="none" stroke="#fff"/><line x1="0.8" y1="5" x2="9.2" y2="5" stroke="#fff"/></svg>
      </span>www.prairielanternpopcorn.com
    </p>
  </div>
  <div class="band-rule"></div>
  <div class="band"><p class="tagline">Worth every handful</p></div>
</section>

<section class="card card-back" aria-label="Business card back">
  <p class="back-name">Prairie Lantern Popcorn</p>
  <p class="back-web">www.prairielanternpopcorn.com</p>
</section>

</body>
</html>
```